African homeware retailer needs a web page design

We need a web page design for a new homeware and accessories store based in Johannesburg, South Africa. Our store carries modern African inspired items from designers that support social development and poverty alleviation initiatives. We have a particular preference for outfits that are centred on the empowerment of women.

Our business celebrates the skill, design and product of African craft and the work of designers looking to take that forward in a socially beneficial way (creating employment, developing skills, supporting local crafts people etc). We aim to carry items and inspirations from all over the African continent.

We would like to see a design that communicates African beauty and elegance without the typical tribal references that are made in reference to African craft or art.

We would like the web page to be stylish, uncomplicated, modern, captivating and appealing to the discerning customer. A similar value proposition is that of http://www.marlowtenwick.example/.

This is an e-commerce website which must be attractive to both individual buyers and design professionals so the website needs to look professional.

Here are links to some websites we like:
http://www.quenbyhollis.example/
http://www.dravelo.example/

Our logo is attached to the brief.

Target Market(s)

Our target market is female, age 20-50. However should not alienate the design conscious male customer therefore

Industry/Entity Type

E-Commerce

Requirements
Must have
• - A featured product banner which includes a photograph and text. This should be easy to edit as we will be changing the featured product regularly
- An easily expendable products section with categories. Examples of categories could be cushions, bedding, crockery etc. Should be easy to add new categories as well as new product pictures
- Home/landing page should be uncluttered
- Should use the logo and should be easy to change the logo which we have in various colour combinations. We plan to change the logo colours depending on circumstance e.g. make it red and white around Valentines day (similar to the way Vintrel frequently changes the logo on their landing page)

```html
<!DOCTYPE html>
<html lang="en">
<head>
<meta charset="utf-8">
<title>Amani Nest – Homeware &amp; Accessories</title>
<link href="https://fonts.googleapis.com/css2?family=Oxygen:wght@400;700&family=Open+Sans:ital,wght@0,400;0,600;1,400&display=swap" rel="stylesheet">
<style>
  :root{
    --cream:#fcf5d9;
    --cream-deep:#f3ead0;
    --green:#3f8f42;
    --green-dark:#2a6d2e;
    --navy:#1d4b6a;
    --navy-deep:#123d57;
    --ink:#222;
    --grey:#777;
    --line:#d8cfae;
    --white:#fff;
    --orange:#f2a531;
  }
  *{box-sizing:border-box;margin:0;padding:0}
  html,body{width:902px;height:1200px;overflow:hidden}
  body{position:relative;background:var(--white);font-family:"Open Sans",Arial,sans-serif;color:var(--ink)}
  a{color:inherit;text-decoration:none}

  /* header */
  .site-header{position:absolute;left:0;top:0;width:902px;height:90px;background:var(--cream)}
  .brand{position:absolute;left:80px;top:30px}
  .brand-name{font-family:"Oxygen",sans-serif;font-weight:700;font-size:24px;line-height:28px;color:var(--navy)}
  .account-links{position:absolute;right:87px;top:10px;font-size:10.5px;color:var(--ink)}
  .account-links span{margin:0 7px;color:#555}
  .search{position:absolute;left:623px;top:52px;width:200px;height:24px;border:1px solid #ccc;border-radius:12px;background:var(--white)}
  .search span{position:absolute;left:13px;top:4px;font-size:9.5px;font-style:italic;color:#666}
  .search svg{position:absolute;right:7px;top:4px}

  /* nav */
  .main-nav{position:absolute;left:0;top:90px;width:902px;height:38px;background:linear-gradient(#52a055,#2f7a33);display:flex;justify-content:center;align-items:center}
  .main-nav a{font-family:"Oxygen",sans-serif;color:var(--white);font-size:12.5px;padding:0 16px;border-left:1px solid rgba(255,255,255,.45);line-height:12px}
  .main-nav a:first-child{border-left:0}

  /* hero */
  .hero{position:absolute;left:0;top:128px;width:902px;height:321px;background:linear-gradient(#fff 60%,#efefef);border-bottom:1px solid #ddd}
  .hero-photo{position:absolute;left:440px;top:10px;width:380px;height:311px;background:linear-gradient(120deg,#f9f9f9 10%,#e86dc7 40%,#c8e13a 60%,#f5a623 85%);opacity:.85}
  .hero-title{position:absolute;left:83px;top:82px;font-family:"Oxygen",sans-serif;font-size:29px;line-height:34px;font-weight:700;color:var(--navy)}
  .hero-title em{display:block;font-style:normal;font-weight:400;color:var(--green)}
  .hero-text{position:absolute;left:84px;top:154px;width:312px;font-size:9.8px;line-height:16px;color:var(--grey)}
  .slider-dots{position:absolute;left:86px;top:213px;display:flex;gap:3px}
  .slider-dots i{width:11px;height:11px;border-radius:50%;background:#ccc}
  .slider-dots i.active{background:var(--green)}

  /* tiles */
  .tile{position:absolute;width:235px;height:200px;border:1px solid #ddd;overflow:hidden}
  .tile-photo{position:absolute;inset:0}
  .tile-caption{position:absolute;left:0;bottom:0;width:100%;height:54px;padding:11px 14px 0}
  .tile-caption h3{font-family:"Oxygen",sans-serif;font-weight:400;font-size:15.5px;line-height:18px}
  .tile-caption p{font-size:9px;margin-top:2px}
  .cap-orange{background:rgba(242,165,49,.9);color:var(--white)}
  .cap-light{background:rgba(255,255,255,.85);color:var(--navy)}
  .cap-light h3{font-weight:700}
  .cap-navy{background:var(--navy-deep);color:var(--white)}
  .cap-green{background:rgba(92,170,100,.85);color:var(--white)}
  .cap-blue{background:rgba(29,75,106,.9);color:var(--white)}
  .cap-orange p,.cap-navy p,.cap-green p,.cap-blue p{color:rgba(255,255,255,.8)}

  .store-finder{position:absolute;left:586px;top:686px;width:235px;height:200px;background:linear-gradient(#52a055,#2a6d2e);padding:11px}
  .store-finder .frame{width:100%;height:100%;border:1px solid rgba(255,255,255,.85);text-align:center;color:var(--white);padding-top:20px}
  .store-finder h3{font-family:"Oxygen",sans-serif;font-weight:400;font-size:25px;line-height:35px}
  .store-finder h3 span{font-size:29px}
  .store-finder p{font-size:9.5px;line-height:14px;color:rgba(255,255,255,.8);margin:8px 14px 0}
  .store-finder .cta{display:inline-block;margin-top:14px;background:#163a1a;font-size:10.5px;padding:5px 12px}

  /* footer */
  .site-footer{position:absolute;left:0;top:935px;width:902px;height:219px;background:linear-gradient(var(--cream-deep) 0%,#f1e8cd 100%);border-top:1px dashed var(--line)}
  .foot-col{position:absolute;top:40px}
  .foot-col h4{font-family:"Oxygen",sans-serif;font-weight:400;font-size:14.5px;color:#333;margin-bottom:7px}
  .foot-col li{list-style:none;font-size:9.8px;line-height:18.3px;color:#444}
  .foot-col p{font-size:9.8px;color:#333}
  .signup{margin-top:7px;width:209px;height:26px;border:1px solid #ddd;background:var(--white);position:relative}
  .signup span{position:absolute;left:8px;top:6px;font-size:9.5px;color:#333}
  .signup b{position:absolute;right:4px;top:3px;background:var(--green-dark);color:var(--white);font-size:9.5px;padding:2px 8px;font-weight:600}
  .socials{display:flex;gap:3px;margin-top:10px}
  .socials i{width:25px;height:25px;border-radius:50%;background:#111}

  .legal{position:absolute;left:78px;top:1170px;font-size:9px;color:#666}
</style>
</head>
<body>

<header class="site-header">
  <a class="brand" href="#"><span class="brand-name">Amani Nest</span></a>
  <nav class="account-links"><a href="#">My Account</a><span>|</span><a href="#">Wish List</a><span>|</span><a href="#">My Cart</a><span>|</span><a href="#">Login</a></nav>
  <div class="search"><span>Search here..</span>
    <svg width="15" height="15" viewBox="0 0 15 15"><circle cx="6" cy="6" r="4.8" fill="none" stroke="#2a6d2e" stroke-width="2"/><line x1="9.5" y1="9.5" x2="13.5" y2="13.5" stroke="#2a6d2e" stroke-width="2.2" stroke-linecap="round"/></svg>
  </div>
</header>

<nav class="main-nav">
  <a href="#">HOME</a><a href="#">ABOUT</a><a href="#">PRODUCTS</a><a href="#">BEST SELLINGS</a><a href="#">CATEGORIES</a><a href="#">TESTIMONIALS</a><a href="#">SUPPORT</a><a href="#">CONTACT</a>
</nav>

<section class="hero">
  <div class="hero-photo" role="img" aria-label="Bright pink, lime and orange display boxes holding vases, candles and an orchid"></div>
  <h1 class="hero-title">SELLING HOMEWARE<em>AND ACCESSORIES.</em></h1>
  <p class="hero-text">Maecenas at justo id velit placerat molestie Donec dictum lectus non odio Cras a ante vitae enim iaculis aliquam Mauris nunc quam venenatis nec euismod sit amet egestas placerat es</p>
  <div class="slider-dots"><i class="active"></i><i></i><i></i><i></i></div>
</section>

<a class="tile" href="#" style="left:83px;top:469px">
  <div class="tile-photo" role="img" aria-label="Orange patterned mugs on a wooden tray" style="background:linear-gradient(135deg,#f08a2c,#f7f1e6 55%,#c9a77a)"></div>
  <div class="tile-caption cap-orange"><h3>HOMEWARE PRODUCT</h3><p>Maecenas at justo id velit placerat molestie</p></div>
</a>
<a class="tile" href="#" style="left:334px;top:469px">
  <div class="tile-photo" role="img" aria-label="Stack of colourful patterned cushions" style="background:linear-gradient(135deg,#eee,#e9465f 50%,#f2d23c)"></div>
  <div class="tile-caption cap-light"><h3>BEST SELLINGS</h3><p>Maecenas at justo id velit placerat molestie</p></div>
</a>
<a class="tile" href="#" style="left:582px;top:469px">
  <div class="tile-photo" role="img" aria-label="Red and blue decorated glass goblets" style="background:linear-gradient(90deg,#e84a1c,#2e8fd8 50%,#d62020)"></div>
  <div class="tile-caption cap-navy"><h3>NEW ARRIVAL</h3><p>Maecenas at justo id velit placerat molestie</p></div>
</a>
<a class="tile" href="#" style="left:87px;top:686px">
  <div class="tile-photo" role="img" aria-label="White and red glass vases" style="background:linear-gradient(90deg,#f4efe8,#d8302c 65%,#f1e9df)"></div>
  <div class="tile-caption cap-green"><h3>FURNITURE &amp; ACCESSORIES</h3><p>Maecenas at justo id velit placerat molestie</p></div>
</a>
<a class="tile" href="#" style="left:338px;top:686px">
  <div class="tile-photo" role="img" aria-label="Grey pleated cushion on a knitted throw" style="background:linear-gradient(160deg,#9a9a9a,#4d4d4d 55%,#b8b8b8)"></div>
  <div class="tile-caption cap-blue"><h3>FURNITURE &amp; ACCESSORIES</h3><p>Maecenas at justo id velit placerat molestie</p></div>
</a>

<aside class="store-finder">
  <div class="frame">
    <h3>FIND NEAREST<br><span>STORE</span></h3>
    <p>Morbi ornare gravida elit Integer congue augue et malesuada iaculis</p>
    <a class="cta" href="#">CLICK HERE</a>
  </div>
</aside>

<footer class="site-footer">
  <div class="foot-col" style="left:81px">
    <h4>NEWSLETTER SIGN UP</h4>
    <p>Please subscribe here for latest offers.</p>
    <div class="signup"><span>Email address</span><b>SIGN UP</b></div>
    <div class="socials"><i></i><i></i><i></i><i></i></div>
  </div>
  <div class="foot-col" style="left:324px">
    <h4>COMPANY</h4>
    <ul><li>About Us</li><li>Why Choose Us</li><li>By Category</li><li>Best Sellings</li><li>How to Buy</li></ul>
  </div>
  <div class="foot-col" style="left:451px">
    <h4>BEST SELLINGS</h4>
    <ul><li>Phasellus felis dolor</li><li>Scelerisque tempus eget</li><li>Lobortis id libero</li><li>Aliquam nec</li><li>Erat at purus</li></ul>
  </div>
  <div class="foot-col" style="left:599px">
    <h4>SUB LINKS</h4>
    <ul><li>Phasellus felis dolor</li><li>Scelerisque tempus eget</li><li>Lobortis id libero</li><li>Aliquam nec</li><li>Erat at purus</li></ul>
  </div>
  <div class="foot-col" style="left:740px">
    <h4>SUPPORT</h4>
    <ul><li>Customer Support</li><li>FAQ</li><li>Free Shipping</li><li>Return Policy</li><li>Order Now</li></ul>
  </div>
</footer>

<p class="legal">© 2014 Company Name &nbsp;All right reserved &nbsp;Term of Use</p>

</body>
</html>
```